Landscape design build company door flyer

I would like this flyer to convey a high-level of professionalism for a company that is excellent with communication with their clients as well as a company that does incredible installations

Went on vacation/holiday

```html
<!DOCTYPE html>
<html lang="en">
<head>
<meta charset="utf-8">
<title>Cedarline Builders – Outdoor Living Flyer</title>
<link rel="stylesheet" href="https://fonts.googleapis.com/css2?family=Montserrat:wght@400;500;600;700;800;900&display=swap">
<style>
  :root {
    --ink: #0c0c0c;
    --orange: #f26f12;
    --navy: #1d2f46;
    --paper: #ffffff;
    --backdrop: #9c9c9c;
    --text: #1a1a1a;
  }
  * { box-sizing: border-box; margin: 0; padding: 0; }
  html, body {
    width: 1200px; height: 933px; overflow: hidden;
    background: var(--backdrop);
    font-family: "Montserrat", sans-serif;
  }
  .flyer {
    position: absolute; left: 253px; top: 20px;
    width: 1178px; height: 1515px;
    background: var(--paper);
    transform: scale(0.5894); transform-origin: top left;
    overflow: hidden;
  }
  .abs { position: absolute; }
  .nowrap { white-space: nowrap; }

  /* brand block */
  .brand { left: 20px; top: 140px; width: 370px; text-align: center; color: var(--navy); white-space: nowrap; }
  .brand-dot { width: 80px; height: 80px; border-radius: 50%; background: var(--navy); margin: 0 auto 28px; }
  .brand-name { font-weight: 700; font-size: 24px; letter-spacing: 0.3px; line-height: 1; }
  .brand-tag { font-weight: 700; font-size: 15px; letter-spacing: 0.2px; margin-top: 8px; }

  .shapes { left: 0; top: 0; width: 1178px; height: 1515px; }

  /* headline */
  .headline { left: 495px; top: 72px; line-height: 1; white-space: nowrap; }
  .headline .line1 { font-weight: 800; font-size: 80px; letter-spacing: 3px; color: var(--ink); }
  .headline .line2 { font-weight: 900; font-size: 146px; letter-spacing: 4px; color: var(--orange); margin-top: -4px; }

  .band-text { left: 498px; top: 306px; color: #fff; font-weight: 700; font-size: 45px; line-height: 47px; letter-spacing: 0.8px; white-space: nowrap; }

  /* photos */
  .photo { position: absolute; }
  .photo-hero { left: 17px; top: 369px; width: 1161px; height: 397px;
    background: linear-gradient(90deg, #5f7a34 0%, #7d8a45 22%, #a97845 32%, #3a414a 45%, #4a4f55 62%, #a56f3f 74%, #2a2d33 85%, #9aa3ad 100%); }
  .photo-frame { left: 52px; top: 674px; width: 449px; height: 189px; background: #fff; padding: 6px; }
  .photo-frame .fill { width: 100%; height: 100%;
    background: linear-gradient(135deg, #5a6b3a 0%, #8c8b86 40%, #b9bcbd 60%, #6f6a4a 100%); }
  .photo-deck { left: 58px; top: 886px; width: 436px; height: 179px;
    background: linear-gradient(180deg, #4b5a3f 0%, #b98e6c 35%, #c49a78 55%, #8d9288 80%, #5e7a3a 100%); }
  .photo-platform { left: 58px; top: 1092px; width: 436px; height: 178px;
    background: linear-gradient(180deg, #9a958a 0%, #b4afa4 28%, #a68567 45%, #8d6a4e 70%, #b7a58a 100%); }

  /* about + services */
  .section-title { font-weight: 800; font-size: 31px; color: var(--ink); letter-spacing: 0.3px; line-height: 1.1; white-space: nowrap; }
  .rule { position: relative; width: 568px; height: 3px; background: var(--ink); margin-top: 6px; }
  .rule::before { content: ""; position: absolute; left: 0; top: -1px; width: 140px; height: 5px; background: var(--orange); }
  .about { left: 540px; top: 800px; width: 568px; }
  .about p { margin-top: 10px; padding-left: 3px; font-size: 18.4px; line-height: 24.7px; color: var(--text);
    text-align: justify; hyphens: auto; letter-spacing: 0.2px; }
  .services { left: 540px; top: 1104px; width: 620px; }
  .service-list { list-style: none; display: grid; grid-template-columns: 310px 310px; grid-auto-flow: column;
    grid-template-rows: repeat(4, 36.5px); margin-top: 22px; }
  .service-list li { display: flex; align-items: center; gap: 16px; font-weight: 500; font-size: 20.5px; color: var(--ink); letter-spacing: 0.3px; white-space: nowrap; }
  .service-list svg { width: 20px; height: 20px; flex: none; }

  /* footer */
  .cta-band { left: 0; top: 1319px; width: 1178px; height: 95px; background: var(--ink); color: #fff;
    display: flex; align-items: center; justify-content: center; font-weight: 800; font-size: 41px; letter-spacing: 1px; white-space: nowrap; }
  .contact { left: 0; top: 1418px; width: 1178px; height: 64px; display: flex; align-items: center; justify-content: center; gap: 22px;
    color: var(--ink); font-weight: 700; white-space: nowrap; }
  .contact-item { display: flex; align-items: center; gap: 10px; }
  .contact-item svg { width: 22px; height: 22px; }
  .contact .phone { font-size: 29px; }
  .contact .small { font-size: 19px; letter-spacing: 0.3px; }
  .divider { width: 3px; height: 34px; background: var(--ink); }
</style>
</head>
<body>
<div class="flyer">
  <div class="photo photo-hero" role="img" aria-label="Photo of a covered patio with timber posts, stone bar, outdoor seating and paver floor"></div>

  <svg class="abs shapes" viewBox="0 0 1178 1515" aria-hidden="true">
    <polygon points="258,0 290,0 462,213 396,296 364,296 430,213" fill="var(--ink)"/>
    <polygon points="367,295 1178,295 1178,425 258,425" fill="var(--ink)"/>
  </svg>

  <div class="abs brand">
    <div class="brand-dot"></div>
    <div class="brand-name">CEDARLINE BUILDERS</div>
    <div class="brand-tag">OUTDOOR LIVING SPACES</div>
  </div>

  <h1 class="abs headline">
    <div class="line1">LOVE COMING</div>
    <div class="line2">HOME?</div>
  </h1>

  <div class="abs band-text">LET US REIMAGINE YOUR<br>OUTDOOR LIVING AREA</div>

  <div class="photo photo-frame"><div class="fill" role="img" aria-label="Photo of a paver walkway and steps through a planted garden slope"></div></div>
  <div class="photo photo-deck" role="img" aria-label="Photo of a two-level cedar deck with stairs and railings"></div>
  <div class="photo photo-platform" role="img" aria-label="Photo of a low stepped composite deck platform behind a house"></div>

  <section class="abs about">
    <h2 class="section-title">ABOUT US</h2>
    <div class="rule"></div>
    <p>Discover the endless possibilities for your outdoor space with The Cedarline Builders Team. Our team of skilled artisans is dedicated to turning your outdoor space into a breathtaking oasis that you’ll love coming home to. Whether it’s a cozy patio for intimate gatherings, a sprawling deck to host memorable parties, or a custom paver driveway that adds instant curb appeal, our high-quality craftsmanship ensures stunning results that exceed your expectations.</p>
  </section>

  <section class="abs services">
    <h2 class="section-title">OUR SERVICES</h2>
    <div class="rule"></div>
    <ul class="service-list">
      <li><svg viewBox="0 0 22 22"><circle cx="11" cy="11" r="10" fill="var(--orange)"/><path d="M6.5 11.3l3 3 6-6.3" fill="none" stroke="#fff" stroke-width="2.6" stroke-linecap="round" stroke-linejoin="round"/></svg>PAVER PATIOS</li>
      <li><svg viewBox="0 0 22 22"><circle cx="11" cy="11" r="10" fill="var(--orange)"/><path d="M6.5 11.3l3 3 6-6.3" fill="none" stroke="#fff" stroke-width="2.6" stroke-linecap="round" stroke-linejoin="round"/></svg>PAVER DRIVEWAYS</li>
      <li><svg viewBox="0 0 22 22"><circle cx="11" cy="11" r="10" fill="var(--orange)"/><path d="M6.5 11.3l3 3 6-6.3" fill="none" stroke="#fff" stroke-width="2.6" stroke-linecap="round" stroke-linejoin="round"/></svg>RETAINING WALLS</li>
      <li><svg viewBox="0 0 22 22"><circle cx="11" cy="11" r="10" fill="var(--orange)"/><path d="M6.5 11.3l3 3 6-6.3" fill="none" stroke="#fff" stroke-width="2.6" stroke-linecap="round" stroke-linejoin="round"/></svg>DECKS &amp; RAILINGS</li>
      <li><svg viewBox="0 0 22 22"><circle cx="11" cy="11" r="10" fill="var(--orange)"/><path d="M6.5 11.3l3 3 6-6.3" fill="none" stroke="#fff" stroke-width="2.6" stroke-linecap="round" stroke-linejoin="round"/></svg>POOLS</li>
      <li><svg viewBox="0 0 22 22"><circle cx="11" cy="11" r="10" fill="var(--orange)"/><path d="M6.5 11.3l3 3 6-6.3" fill="none" stroke="#fff" stroke-width="2.6" stroke-linecap="round" stroke-linejoin="round"/></svg>OUTDOOR LIGHTING</li>
      <li><svg viewBox="0 0 22 22"><circle cx="11" cy="11" r="10" fill="var(--orange)"/><path d="M6.5 11.3l3 3 6-6.3" fill="none" stroke="#fff" stroke-width="2.6" stroke-linecap="round" stroke-linejoin="round"/></svg>FIREPITS &amp; FIREPLACES</li>
      <li><svg viewBox="0 0 22 22"><circle cx="11" cy="11" r="10" fill="var(--orange)"/><path d="M6.5 11.3l3 3 6-6.3" fill="none" stroke="#fff" stroke-width="2.6" stroke-linecap="round" stroke-linejoin="round"/></svg>AND MORE...</li>
    </ul>
  </section>

  <div class="abs cta-band">CONTACT US TODAY FOR A FREE ESTIMATE</div>

  <div class="abs contact">
    <div class="contact-item phone">
      <svg viewBox="0 0 24 24"><path d="M6.6 2.5l3 .4 1.3 4.6-2.2 1.6c1.2 2.7 3.2 4.7 5.9 5.9l1.6-2.2 4.6 1.3.4 3c.1 1-.7 1.9-1.7 1.9C10.6 19 5 13.4 4.7 4.2c0-1 .9-1.8 1.9-1.7z" fill="var(--orange)"/></svg>
      206-555-0148
    </div>
    <div class="divider"></div>
    <div class="contact-item small">
      <svg viewBox="0 0 24 24"><rect x="2" y="5" width="20" height="14" rx="1.5" fill="var(--orange)"/><path d="M3 6.5l9 6.5 9-6.5" fill="none" stroke="#fff" stroke-width="1.8"/></svg>
      INFO@CEDARLINEBUILDERS.COM
    </div>
    <div class="divider"></div>
    <div class="contact-item small">
      <svg viewBox="0 0 24 24" fill="none" stroke="var(--orange)" stroke-width="1.6"><circle cx="12" cy="12" r="9.5"/><ellipse cx="12" cy="12" rx="4.2" ry="9.5"/><path d="M2.5 12h19M4 7h16M4 17h16"/></svg>
      WWW.CEDARLINEBUILDERS.COM
    </div>
  </div>
</div>
</body>
</html>
```